Social Media Graphics - Oakline Push REVISED

Create 6-7 individual social media graphics (square size) to encourage folks to join our online course called:

The Harvest Ledger Circle
How to Launch a Multi-Million Business From Scratch
Sign Up Today!

IMPORTANT: Make the largest and most prominent text on the graphic be: How to Launch a Multi-Million Business From Scratch

For the color scheme of the graphics, let's try a blue color palette; make sure the graphics appeal to both men and women

Make sure each graphic contains 1 of the 3 pics attached (crop pic as needed); and make sure one of the graphics is all TEXT only.

Target Market(s)

men and women looking to start a business

Industry/Entity Type

Entrepreneurship

Colors
0054AA
0677BA
7BADD7
CADEEF
E8F1F8

Requirements
Must have
• All the text and use the 3 pics provided; one graphic can be all text; Simple, modern design that's easy to read

```html
<!DOCTYPE html>
<html lang="en">
<head>
<meta charset="utf-8">
<title>The Harvest Ledger Circle – Sign Up Today</title>
<link rel="stylesheet" href="https://fonts.googleapis.com/css2?family=Montserrat:wght@800;900&display=swap">
<style>
  :root {
    --blue-deep: #233f8c;
    --blue-mid: #2c4fa6;
    --blue-bright: #2f7fd6;
    --blue-line: rgba(123, 173, 215, 0.35);
    --band-dark: #2a1513;
    --band-red: #7d1419;
    --white: #ffffff;
    --photo-a: #c9405e;
    --photo-b: #2a2730;
  }
  * { margin: 0; padding: 0; box-sizing: border-box; }
  html, body { width: 1200px; height: 1200px; overflow: hidden; }
  body { font-family: "Montserrat", Arial, sans-serif; color: var(--white); }

  .poster {
    position: relative;
    width: 1200px;
    height: 1200px;
    overflow: hidden;
    background: linear-gradient(135deg, var(--blue-deep) 0%, var(--blue-mid) 55%, var(--blue-deep) 100%);
  }
  .poster-waves { position: absolute; inset: 0; }

  .title-stack {
    position: absolute;
    left: 140px;
    top: 230px;
    width: 330px;
    font-weight: 900;
    line-height: 1;
    text-transform: uppercase;
  }
  .title-stack span { display: block; }
  .title-the { font-size: 52px; letter-spacing: 2px; }
  .title-harvest { font-size: 50px; margin-top: 36px; }
  .title-ledger { font-size: 52px; margin-top: 36px; }

  .host-photo {
    position: absolute;
    left: 494px;
    top: 99px;
    width: 540px;
    height: 526px;
    border-radius: 200px 200px 0 0;
    background: linear-gradient(90deg, var(--photo-a) 0%, var(--photo-a) 48%, var(--photo-b) 52%, var(--photo-b) 100%);
    opacity: 0.9;
  }

  .name-band {
    position: absolute;
    left: 62px;
    top: 624px;
    width: 1075px;
    height: 128px;
    border-radius: 54px;
    background: var(--band-dark);
    box-shadow: 0 -12px 0 var(--band-red);
    display: flex;
    align-items: center;
    justify-content: center;
    font-weight: 900;
    font-size: 52px;
    letter-spacing: 6px;
    text-transform: uppercase;
  }

  .headline {
    position: absolute;
    left: 0;
    top: 784px;
    width: 1200px;
    text-align: center;
    font-weight: 900;
    font-size: 56px;
    line-height: 72px;
    text-transform: uppercase;
  }

  .cta-divider {
    position: absolute;
    left: 87px;
    top: 962px;
    width: 1026px;
    height: 2px;
    background: var(--white);
  }

  .signup-button {
    position: absolute;
    left: 255px;
    top: 1004px;
    width: 689px;
    height: 72px;
    border-radius: 36px;
    background: var(--band-dark);
    display: flex;
    align-items: center;
    justify-content: center;
    font-weight: 900;
    font-size: 40px;
    letter-spacing: 7px;
    text-transform: uppercase;
  }
</style>
</head>
<body>
<main class="poster">
  <svg class="poster-waves" width="1200" height="1200" viewBox="0 0 1200 1200" aria-hidden="true">
    <path d="M900 0 C1100 300 1000 700 1200 900 L1200 0 Z" fill="#2a56b0" opacity="0.5"/>
    <path d="M0 1200 C300 900 700 1050 1200 700 L1200 1200 Z" fill="#2850a8" opacity="0.45"/>
    <path d="M600 1200 C800 1000 1000 900 1200 760 L1200 1200 Z" fill="var(--blue-bright)" opacity="0.35"/>
    <g fill="none" stroke="var(--blue-line)" stroke-width="1.5">
      <path d="M0 700 C200 660 400 680 600 760"/>
      <path d="M0 740 C200 700 400 720 600 800"/>
      <path d="M0 780 C200 740 400 760 600 840"/>
      <path d="M0 820 C200 780 400 800 600 880"/>
      <path d="M0 860 C200 820 400 840 600 920"/>
      <path d="M0 900 C200 860 400 880 600 960"/>
      <path d="M1040 0 C1160 300 1100 600 1200 800"/>
      <path d="M1080 0 C1190 300 1140 600 1200 700"/>
    </g>
  </svg>

  <div class="title-stack">
    <span class="title-the">The</span>
    <span class="title-harvest">Harvest</span>
    <span class="title-ledger">Ledger</span>
  </div>

  <div class="host-photo" role="img" aria-label="Photo of the two course hosts smiling, a woman in a pink dress with arms crossed and a man in a black jacket"></div>

  <div class="name-band">Circle</div>

  <h1 class="headline">How to launch a multi-million<br>business from scratch</h1>

  <div class="cta-divider" aria-hidden="true"></div>

  <div class="signup-button">Sign up today</div>
</main>
</body>
</html>
```